Tall Fern Roofing Business Card

Need a business card with the logo that was designed here

Contact Information for Business Card

Name, Title, Phone, Email, Website, Company name

```html
<!DOCTYPE html>
<html lang="en">
<head>
<meta charset="UTF-8">
<title>Tall Fern Roofing – Business Card</title>
<link rel="stylesheet" href="https://fonts.googleapis.com/css2?family=Oswald:wght@500&family=Poppins:wght@400;500&display=swap">
<style>
  :root {
    --page-bg: #262626;
    --card-bg: #121212;
    --brand-blue: #1f74bf;
    --band-grey: #9b9ca0;
    --text-light: #f2f2f2;
    --divider: #8a8a8a;
  }
  * { box-sizing: border-box; margin: 0; padding: 0; }
  html, body {
    width: 1200px; height: 900px; overflow: hidden;
    background: var(--page-bg);
  }
  .sheet {
    width: 1200px; height: 900px;
    display: flex; flex-direction: column; align-items: center; justify-content: center;
    gap: 44px;
  }
  .card {
    position: relative;
    width: 620px; height: 354px;
    background: var(--card-bg);
    box-shadow: 0 10px 28px rgba(0,0,0,.55);
    overflow: hidden;
  }
  .card__band {
    position: absolute; left: 0; right: 0; bottom: 0; height: 12px;
  }
  .card--front .card__band { background: var(--brand-blue); }
  .card--back .card__band { background: var(--band-grey); }

  /* Front */
  .brand {
    position: absolute; inset: 0 0 12px 0;
    display: flex; align-items: center; justify-content: center; gap: 12px;
  }
  .brand__mark {
    width: 18px; height: 18px; background: var(--brand-blue);
  }
  .brand__name {
    font-family: "Poppins", sans-serif; font-weight: 500;
    font-size: 34px; letter-spacing: 1px;
    color: var(--brand-blue);
  }

  /* Back */
  .person {
    position: absolute; left: 52px; top: 132px;
  }
  .person__name {
    font-family: "Oswald", sans-serif; font-weight: 500;
    font-size: 34px; line-height: 1; text-transform: uppercase;
    color: var(--brand-blue);
  }
  .person__title {
    font-family: "Poppins", sans-serif; font-weight: 400;
    font-size: 16px; color: var(--text-light); margin-top: 4px; padding-left: 6px;
  }
  .divider {
    position: absolute; left: 300px; top: 120px; width: 1px; height: 92px;
    background: var(--divider);
  }
  .contacts {
    position: absolute; left: 328px; top: 124px;
    list-style: none; display: flex; flex-direction: column; gap: 8px;
  }
  .contacts__item {
    display: flex; align-items: center; gap: 10px;
    font-family: "Poppins", sans-serif; font-size: 16px; color: var(--text-light);
  }
  .contacts__icon { width: 16px; height: 16px; flex: none; }
</style>
</head>
<body>
<main class="sheet">
  <section class="card card--front">
    <div class="brand">
      <span class="brand__mark"></span>
      <span class="brand__name">Tall Fern Roofing</span>
    </div>
    <div class="card__band"></div>
  </section>

  <section class="card card--back">
    <div class="person">
      <h1 class="person__name">Marcus Hale</h1>
      <p class="person__title">Managing Director</p>
    </div>
    <div class="divider"></div>
    <ul class="contacts">
      <li class="contacts__item">
        <svg class="contacts__icon" viewBox="0 0 24 24" fill="none" stroke="#1f74bf" stroke-width="2.2" stroke-linejoin="round">
          <path d="M5 3h4l2 5-2.5 1.5a11 11 0 0 0 6 6L16 13l5 2v4a2 2 0 0 1-2 2A16 16 0 0 1 3 5a2 2 0 0 1 2-2z"/>
        </svg>
        044-987 650 321
      </li>
      <li class="contacts__item">
        <svg class="contacts__icon" viewBox="0 0 24 24" fill="#1f74bf">
          <path d="M2 5h20v14H2z"/>
          <path d="M2 5l10 8 10-8" fill="none" stroke="#121212" stroke-width="2"/>
        </svg>
        info@tallfernroofing.com
      </li>
      <li class="contacts__item">
        <svg class="contacts__icon" viewBox="0 0 24 24" fill="none" stroke="#1f74bf" stroke-width="2">
          <circle cx="12" cy="12" r="10"/>
          <ellipse cx="12" cy="12" rx="4.5" ry="10"/>
          <path d="M2 12h20M4 7h16M4 17h16"/>
        </svg>
        www.tallfernroofing.com
      </li>
    </ul>
    <div class="card__band"></div>
  </section>
</main>
</body>
</html>
```